MRT Property - Business Cards

Looking for a business card & general letterhead, signage etc design for our new logo.

Colours:
000a20
0056a2
00b5ef
0088ce
68cef2

Fonts:
Poppins
Karla

Please keep look and feel of new brand - example in the zip package I sent.

```html
<!DOCTYPE html>
<html lang="en">
<head>
<meta charset="UTF-8">
<title>MRT Property – Business Cards</title>
<link href="https://fonts.googleapis.com/css2?family=Poppins:wght@400;500;700;800&display=swap" rel="stylesheet">
<style>
  :root{
    --navy:#000a20;
    --royal:#0056a2;
    --sky:#00b5ef;
    --ocean:#0088ce;
    --ice:#68cef2;
    --paper:#ffffff;
    --stage:#2a2c31;
  }
  *{margin:0;padding:0;box-sizing:border-box}
  html,body{width:1200px;height:900px;overflow:hidden}
  body{
    background:var(--stage);
    font-family:'Poppins',sans-serif;
    display:flex;align-items:center;justify-content:center;gap:60px;
  }
  .card{
    position:relative;
    width:520px;height:297px;
    background:var(--navy);
    border-radius:22px;
    overflow:hidden;
    box-shadow:0 18px 40px rgba(0,0,0,.45);
  }
  /* front */
  .card-front .brand{
    position:absolute;left:28px;top:84px;width:196px;
    display:flex;align-items:center;gap:8px;
  }
  .brand-dot{width:18px;height:18px;border-radius:50%;background:var(--ice);flex:none}
  .brand-name{
    color:var(--royal);font-weight:800;font-size:21px;line-height:1;letter-spacing:0;white-space:nowrap;
  }
  .divider{
    position:absolute;left:240px;top:40px;width:2px;height:170px;
    background:var(--ocean);
  }
  .details{
    position:absolute;left:262px;top:44px;right:20px;color:var(--paper);
  }
  .person-name{color:var(--royal);font-weight:700;font-size:19px;letter-spacing:.5px;text-transform:uppercase;line-height:1.1}
  .person-role{font-size:13px;margin-top:2px}
  .address{font-size:13px;line-height:1.35;margin-top:12px}
  .contacts{list-style:none;margin-top:8px;font-size:13px;line-height:1.55}
  .contacts li{display:flex;align-items:center;gap:7px}
  .contacts svg{width:12px;height:12px;flex:none}
  .band{position:absolute;left:0;right:0;bottom:0;height:30px;display:flex}
  .band-light{width:38%;background:var(--ice)}
  .band-dark{flex:1;background:var(--ocean);border-left:3px solid var(--navy)}
  /* back */
  .card-back{display:flex;align-items:center;justify-content:center}
  .card-back .brand{display:flex;align-items:center;gap:16px}
  .card-back .brand-dot{width:40px;height:40px}
  .card-back .brand-name{font-size:50px}
</style>
</head>
<body>
  <section class="card card-front">
    <div class="brand">
      <span class="brand-dot"></span>
      <span class="brand-name">MRT Property</span>
    </div>
    <div class="divider"></div>
    <div class="details">
      <p class="person-name">Daniel Hayes</p>
      <p class="person-role">Managing Director</p>
      <p class="address">Your address, City<br>State, Zip 1234</p>
      <ul class="contacts">
        <li>
          <svg viewBox="0 0 12 12"><circle cx="6" cy="6" r="6" fill="var(--ocean)"/><path d="M4 3.2l1 1.4-.6.7a4 4 0 0 0 2.3 2.3l.7-.6 1.4 1-.6 1C6 9 3 6 3.3 3.8z" fill="#fff"/></svg>
          555 014 287
        </li>
        <li>
          <svg viewBox="0 0 12 12"><circle cx="6" cy="6" r="6" fill="var(--ocean)"/><rect x="3" y="4" width="6" height="4.2" fill="#fff"/><path d="M3 4l3 2.3L9 4" fill="none" stroke="var(--ocean)" stroke-width=".8"/></svg>
          info@mrtproperty.com
        </li>
        <li>
          <svg viewBox="0 0 12 12"><circle cx="6" cy="6" r="6" fill="var(--ocean)"/><circle cx="6" cy="6" r="3" fill="none" stroke="#fff" stroke-width=".9"/><path d="M3 6h6M6 3v6" stroke="#fff" stroke-width=".7"/></svg>
          www.mrtproperty.com
        </li>
      </ul>
    </div>
    <div class="band"><span class="band-light"></span><span class="band-dark"></span></div>
  </section>

  <section class="card card-back">
    <div class="brand">
      <span class="brand-dot"></span>
      <span class="brand-name">MRT Property</span>
    </div>
  </section>
</body>
</html>
```